Vernac Law Business cards and stationary design project

We are looking for a stationary design for business cards (double sided), 8x10, 5x7, and legal and standard envelopes.

We would like the design to match the logo that we have already.
Color palate preferred is Teal, White, grey and any others that will look good for a professional law firm.

We would like this statement: "RELATIONSHIPS. RESPECT. RESULT" to be on the back of the business cards and maybe on the stationary if it looks good.

Please see link to website for more information: www.vernac-law.example

Target Market(s)

Potential clients that need Attorney services.

Industry/Entity Type

Law Firm

Contact Information for Business Card

We would like the front and back to be two different colors. Current business cards are teal front, grey back and are a vertical design. We are open to options with colors.

Font styles to use
Serif

Colors
33a6d7
33b8a4
b9b9b9
5c5c5c

Requirements
Must have
• Logo supplied needs to go on the card and stationary.
• Match website color palate, www.vernac-law.example
• Be professional and not too wordy.
• Criminal Law, Civil Litigation, Personal Injury, Restraining Orders need to be on the card.
Nice to have
• RELATIONSHIPS. RESPECT. RESULTS. on the back of the card.
Should not have
• Not be too busy/wordy or too flashy.

```html
<!DOCTYPE html>
<html lang="en">
<head>
<meta charset="utf-8">
<title>Vernac Law — Business Card, Front and Back</title>
<link href="https://fonts.googleapis.com/css2?family=Open+Sans:wght@400;600&display=swap" rel="stylesheet">
<style>
  :root {
    --teal: #0f8899;
    --white: #ffffff;
    --ink: #1f2a2e;
    --backdrop: #eceeef;
  }
  * { box-sizing: border-box; margin: 0; padding: 0; }
  html, body { width: 1200px; height: 900px; overflow: hidden; }
  body {
    background: var(--backdrop);
    font-family: "Open Sans", Arial, sans-serif;
    position: relative;
  }
  .card {
    position: absolute;
    border-radius: 16px;
    overflow: hidden;
    box-shadow: 0 6px 18px rgba(0,0,0,0.12);
  }
  .card--front { left: 78px; top: 34px; width: 588px; height: 364px; background: var(--white); }
  .card--back { left: 390px; top: 506px; width: 565px; height: 350px; background: var(--teal); }

  .band { position: absolute; left: 0; width: 100%; }
  .card--front .band { top: 30px; height: 98px; background: var(--teal); }
  .card--back .band { top: 80px; height: 96px; background: var(--white); }

  .emblem-circle { position: absolute; border-radius: 50%; }
  .card--front .emblem-circle { left: 232px; top: 12px; width: 136px; height: 136px; background: var(--white); }
  .card--back .emblem-circle { left: 220px; top: 57px; width: 130px; height: 130px; background: var(--teal); }

  .firm-name {
    position: absolute; left: 0; width: 100%;
    text-align: center;
    font-weight: 400;
    font-size: 29px;
    letter-spacing: 2px;
    text-transform: uppercase;
  }
  .card--front .firm-name { top: 136px; color: var(--teal); }
  .card--back .firm-name { top: 180px; color: var(--white); font-size: 28px; }

  .person {
    position: absolute; right: 320px; top: 218px;
    text-align: right; color: var(--ink);
  }
  .person__name { font-size: 23px; color: var(--teal); line-height: 30px; }
  .person__title { font-size: 15px; line-height: 20px; margin-bottom: 10px; }
  .person__address { font-size: 15px; line-height: 19px; }

  .contact-list {
    position: absolute; left: 306px; top: 219px;
    list-style: none; color: var(--ink);
    font-size: 15px;
  }
  .contact-list li { display: flex; align-items: center; height: 24.5px; }
  .contact-list svg { width: 12px; height: 12px; margin-right: 11px; fill: var(--teal); flex: none; }

  .practice-areas {
    position: absolute; left: 0; top: 250px; width: 100%;
    text-align: center; color: var(--white);
    font-size: 15px; font-weight: 600; line-height: 21px;
  }
  .tagline {
    position: absolute; left: 0; top: 307px; width: 100%;
    text-align: center; color: var(--white);
    font-size: 15px; font-weight: 600; letter-spacing: 0.3px;
  }
</style>
</head>
<body>
  <section class="card card--front">
    <div class="band"></div>
    <div class="emblem-circle"></div>
    <h1 class="firm-name">Vernac Law</h1>

    <div class="person">
      <p class="person__name">Daniel Marsh</p>
      <p class="person__title">Managing Director</p>
      <p class="person__address">12345, Address Goes Here<br>Country Name, 123456</p>
    </div>

    <ul class="contact-list">
      <li>
        <svg viewBox="0 0 24 24"><path d="M6.6 10.8a15.1 15.1 0 006.6 6.6l2.2-2.2a1 1 0 011-.25 11.4 11.4 0 003.6.57 1 1 0 011 1V20a1 1 0 01-1 1A17 17 0 013 4a1 1 0 011-1h3.5a1 1 0 011 1c0 1.25.2 2.45.57 3.6a1 1 0 01-.25 1z"/></svg>
        (044)-456-7890
      </li>
      <li>
        <svg viewBox="0 0 24 24"><path d="M6 2h10v6H6z M3 9h18v11H3z M7 13h3v2H7z M12 13h3v2h-3z M7 16h3v2H7z M12 16h3v2h-3z"/></svg>
        123-456-7890
      </li>
      <li>
        <svg viewBox="0 0 24 24"><path d="M2 5h20v14H2z" /><path d="M2 5l10 8 10-8" fill="none" stroke="#fff" stroke-width="2"/></svg>
        info@youremail.com
      </li>
      <li>
        <svg viewBox="0 0 24 24"><circle cx="12" cy="12" r="10"/><path d="M8 7c2 1 3 3 2 5s1 3 3 3M14 4c-1 2 1 3 3 3" fill="none" stroke="#fff" stroke-width="1.8"/></svg>
        www.website.com
      </li>
    </ul>
  </section>

  <section class="card card--back">
    <div class="band"></div>
    <div class="emblem-circle"></div>
    <h2 class="firm-name">Vernac Law</h2>
    <p class="practice-areas">Practice areas, Criminal Law<br>Civil Litigation/Personal Injury, Restraining Orders</p>
    <p class="tagline">RELATIONSHIPS. RESPECT. RESULT</p>
  </section>
</body>
</html>
```